Create Website for new company called "Verdale Lodge 37"

Verdale Lodge 37 is a new business situated in Southwestern Colorado. We are creating a business that will rent out spaces where clients can grow their own marijuana. Picture a large green house with partitioned spaces that are secured by a lock. Best way to envision this would be to think of a storage business that rents out storage rooms. The difference is that we will be having the units inside a green house ( for growing purposes) Picture a small area that is secured by locks, Picture an area that has the ability to provide state of the art security, cameras etc. We want to focus our efforts on professionals, blue collar workers and end users of marijuana. Our emphasis is in the area of assisting those whom wish to grow their own plants. We want to provide them a safe facility in which to do that. . Keep in mind that we also build custom grow rooms at clients homes and provide a grow pod (lease these) where a small grow unit will be delivered and picked up from our clients whom want to lease a unit for a short amount of time. We have a business card ( just designed) and will send that information to those whom express an interests in this project. We want to be able to sign people up for our services by entering an agreement and signing the agreement while on the internet. We want to provide our services to those whom consume recreational and medical marijuana. This site will need to gather information I.e email addresses so that we can followup with offers. This is a tremendous opportunity for the right designer. We will be creating many more websites as other states come on line and make marijuana legal to consume. Use the business card model for a point of reference of how we envision the concept. That is a business card we just recently printed. The hands and the plant is our logo so far. Open to suggestions. There will be three levels of service. Bronze, Silver, Gold or Platinum. We will also have a retail biz down the road but not at the present time.

Target Market(s)

Ages 21-60

Industry/Entity Type

Medical

Logo Text

Verdale Lodge 37.

Number of Pages Required

5+ page

Requirements
Must have
• Clean appearance not to busy , easily navigable from link to link, page to page. Must have ability down the road to enter into a contractual agreement via the website. Must use our provided logo and example of that is on our business card that will be uploaded here shortly. We would like to have the colors that are on the business card however if you have suggestions or color schemes that you want us to consider that is okay.
Nice to have
• Nice to have a animation of seed to weed and how clients can save a tremendous amount of money growing their own cannabis. Nice to have testimonial page or feedback page. Have a membership component to website,
Should not have
• No flashing lights, etc. Not to busy in terms of animations.

```html
<!DOCTYPE html>
<html lang="en">
<head>
<meta charset="utf-8">
<title>Verdale Lodge 37</title>
<link href="https://fonts.googleapis.com/css2?family=Oswald:wght@400;500&family=Lato:ital,wght@0,400;0,700;1,400&display=swap" rel="stylesheet">
<style>
:root{
  --green:#078a3c;
  --green-dark:#036b2c;
  --green-light:#12a04c;
  --ink:#333;
  --muted:#666;
  --paper:#fff;
  --mist:#f3f3f3;
  --footer:#333;
  --panel:#4b4b4b;
  --field:#5c5c5c;
  --head:"Oswald",sans-serif;
  --body:"Lato",sans-serif;
}
*{box-sizing:border-box;margin:0;padding:0}
html,body{width:780px;height:1200px;overflow:hidden}
body{position:relative;font-family:var(--body);color:var(--ink);background:var(--paper)}
.abs{position:absolute}

.topbar{left:0;top:0;width:780px;height:52px;background:linear-gradient(var(--green-light),var(--green-dark))}
.phone{left:85px;top:17px;color:#fff;font-size:16px;display:flex;align-items:center;gap:6px}
.social{display:flex;gap:6px}
.social span{width:22px;height:22px;border-radius:50%;background:#fff;display:block}
.top-social{left:590px;top:15px}

.nav{left:0;top:52px;width:780px;height:36px;background:#fff}
.nav a{position:absolute;top:6px;height:24px;line-height:24px;font-family:var(--head);font-size:10px;color:var(--ink);text-decoration:none;letter-spacing:.3px}
.nav a.sep{border-right:1px solid #ccc;padding-right:10px}
.nav a.active{background:var(--green);color:#fff;width:60px;text-align:center}

.brand{left:300px;top:5px;width:180px;height:100px;background:#fff;border:4px solid #2f9a58;display:flex;flex-direction:column;align-items:center;justify-content:center;gap:6px}
.brand-name{font-family:var(--head);font-weight:500;font-size:21px;color:#3a3a3a}
.brand-tag{font-size:6px;color:#444;letter-spacing:.3px}

.hero{left:0;top:88px;width:780px;height:311px;background:radial-gradient(circle at 50% 40%,#5d8f3a,#2f6b22 55%,#1f4d18)}
.arrow{width:28px;height:28px;border-radius:50%;border:2px solid #ddd;background:rgba(0,0,0,.35);top:229px}
.caption{left:85px;top:317px;width:610px;height:38px;background:rgba(20,30,15,.7);color:#fff;font-family:var(--head);font-size:20px;text-align:center;line-height:36px}

.mist{left:0;top:399px;width:780px;height:208px;background:var(--mist)}
.card{top:363px;width:188px;height:214px;background:#fff;border:1px solid #bbb;border-radius:6px;overflow:hidden;box-shadow:0 10px 8px -8px rgba(0,0,0,.3)}
.card h3{height:37px;background:linear-gradient(var(--green-light),var(--green-dark));color:#fff;font-family:var(--head);font-weight:400;font-size:15px;line-height:37px;padding-left:13px}
.card .shot{margin:9px 9px 0;height:72px;border:3px solid #555}
.card p{font-size:8.9px;line-height:14.5px;color:#555;padding:7px 8px 0 10px;white-space:nowrap}
.more{font-size:8px;font-weight:700;text-decoration:underline;color:var(--ink);display:block}
.card .more{padding:3px 10px}

.welcome{left:0;top:607px;width:780px;height:183px;background:linear-gradient(var(--green-light),var(--green-dark))}
.video{left:85px;top:625px;width:188px;height:146px;background:linear-gradient(#7a8a4c,#3b6a28)}
.video .play{left:82px;top:55px;width:24px;height:24px;border-radius:50%;background:#fff}
.video .bar{left:0;bottom:0;width:188px;height:20px;background:#222;color:#ddd;font-size:7px;display:flex;align-items:center;gap:6px;padding:0 6px}
.video .track{flex:1;height:4px;background:#555;border-radius:2px}
.welcome-title{left:296px;top:624px;font-family:var(--head);font-weight:400;font-size:17px;color:#fff}
.rule-light{left:296px;top:651px;width:399px;height:1px;background:#5cbf84}
.welcome-copy{left:296px;top:662px;width:402px;font-size:9px;line-height:15px;color:#fff}
.welcome-copy p{margin-bottom:14px}
.welcome-copy .more{color:#fff;margin-top:-6px}

.lower{left:0;top:790px;width:780px;height:225px;background:linear-gradient(#fafafa,#dcdcdc)}
.sec-title{font-family:var(--head);font-weight:400;font-size:15px;color:var(--ink);display:flex;align-items:center;gap:8px}
.rule-dark{height:1px;background:#555}
.quote{left:85px;top:854px;width:281px;height:107px;background:#666;border-radius:3px;color:#fff;font-style:italic;font-size:8.9px;line-height:15px;padding:14px 10px 0 18px;text-indent:20px}
.qmark{font-family:Georgia,serif;font-size:26px;color:#ddd;font-style:normal;line-height:1}
.quote-tail{left:110px;top:960px}
.author{left:141px;top:968px;font-size:10px;font-weight:700}
.divider{left:389px;top:805px;width:2px;height:175px;background:linear-gradient(transparent,#c6c6c6,transparent)}
.news{left:414px;width:285px;font-size:8.5px;line-height:13.5px;color:var(--muted);white-space:nowrap}
.news .date{font-weight:700;color:var(--ink);font-size:8.5px;display:flex;align-items:center;gap:5px}
.news .date i{width:7px;height:7px;background:#ccc;display:block}
.news h4{font-size:9.6px;color:#444;padding-left:12px;margin-top:2px}
.news p{padding-left:12px}

footer{color:#fff}
.footer{left:0;top:1015px;width:780px;height:185px;background:var(--footer)}
.quote-panel{left:85px;top:1018px;width:188px;height:182px;background:var(--panel);padding:10px 12px}
.quote-panel h3{font-family:var(--head);font-weight:400;font-size:15px;display:flex;align-items:center;gap:8px;margin-bottom:12px;color:#fff}
.field{width:164px;height:22px;background:var(--field);border:1px solid #777;font-size:7px;color:#bbb;padding:6px 7px;margin-bottom:4px}
.field.tall{height:42px}
.btn{background:var(--green);color:#fff;font-size:10px;text-align:center}
.foot-h{font-family:var(--head);font-weight:400;font-size:13px;color:#fff}
.subscribe{left:296px;top:1052px;display:flex;gap:5px}
.subscribe .input{width:184px;height:24px;background:#5a5a5a;font-size:7px;color:#ddd;padding:8px}
.subscribe .btn{width:55px;height:24px;line-height:24px}
.vline{width:1px;background:#555}
.hline{height:1px;background:#555}
.contact{font-size:9px;line-height:13.5px;display:flex;gap:10px;color:#fff;align-items:flex-start}
.contact svg{flex:none;margin-top:1px}
.foot-brand{left:590px;top:1125px;font-family:var(--head);font-weight:500;font-size:15px;color:#e8e8e8}
.copy{left:305px;top:1177px;font-size:8px;color:#ddd}
</style>
</head>
<body>

<header>
  <div class="abs topbar"></div>
  <div class="abs phone">
    <svg width="18" height="18" viewBox="0 0 18 18"><circle cx="9" cy="9" r="8" fill="none" stroke="#fff" stroke-width="1.5"/><path d="M6 5l2 0 1 2-1 1c.5 1 1.5 2 2.5 2.5l1-1 2 1v2c-4 0-7.5-3.5-7.5-7.5z" fill="#fff"/></svg>
    +123-555-0147
  </div>
  <div class="abs social top-social"><span></span><span></span><span></span><span></span></div>

  <nav class="abs nav">
    <a class="active" style="left:85px">HOME</a>
    <a class="sep" style="left:165px;width:60px">ABOUT US</a>
    <a style="left:245px">SERVICES</a>
    <a class="sep" style="left:499px;width:50px">FACILITIES</a>
    <a class="sep" style="left:559px;width:62px">TESTIMONIAL</a>
    <a class="sep" style="left:634px;width:61px">CONTACT US</a>
  </nav>

  <div class="abs brand">
    <div class="brand-name">VERDALE LODGE 37</div>
    <div class="brand-tag">" supporting the care &amp; cultivation of cannabis "</div>
  </div>
</header>

<section>
  <div class="abs hero" role="img" aria-label="Photo of open hands above a field of cannabis plants"></div>
  <div class="abs arrow" style="left:56px"><svg width="24" height="24"><path d="M14 7l-5 5 5 5" stroke="#fff" stroke-width="2" fill="none"/></svg></div>
  <div class="abs arrow" style="left:695px"><svg width="24" height="24"><path d="M10 7l5 5-5 5" stroke="#fff" stroke-width="2" fill="none"/></svg></div>
  <div class="abs caption">Lorem ipsum dolor sit amet, consectetuer adipiscing elit, sed</div>
</section>

<section>
  <div class="abs mist"></div>
  <article class="abs card" style="left:85px">
    <h3>LEASE</h3>
    <div class="shot" role="img" aria-label="Photo of hands holding soil with a seedling" style="background:linear-gradient(#6c4a33,#3a2a20)"></div>
    <p>Lorem ipsum dolor sit ametuer adipiscingi<br>elit, sed diam nmy nibh euismod tincidunt<br>ut laoreet dolore magna am erat visi enim<br>ad minim veniam, quis nostrud exerci</p>
    <a class="more">READ MORE »</a>
  </article>
  <article class="abs card" style="left:296px">
    <h3>SECURITY</h3>
    <div class="shot" role="img" aria-label="Photo of a security camera mounted on a brick wall" style="background:linear-gradient(90deg,#4d8ed0,#7ab2e6 60%,#9a5a3e)"></div>
    <p>Lorem ipsum dolor sit ametuer adipiscingi<br>elit, sed diam nmy nibh euismod tincidunt<br>ut laoreet dolore magna am erat visi enim<br>ad minim veniam, quis nostrud exerci</p>
    <a class="more">READ MORE »</a>
  </article>
  <article class="abs card" style="left:507px">
    <h3>ONLINE ACCESS</h3>
    <div class="shot" role="img" aria-label="Photo of a screen showing an online account page" style="background:linear-gradient(90deg,#2c3e5a,#e8ecef 25%,#f2f2f2)"></div>
    <p>Lorem ipsum dolor sit ametuer adipiscingi<br>elit, sed diam nmy nibh euismod tincidunt<br>ut laoreet dolore magna am erat visi enim<br>ad minim veniam, quis nostrud exerci</p>
    <a class="more">READ MORE »</a>
  </article>
</section>

<section>
  <div class="abs welcome"></div>
  <div class="abs video" role="img" aria-label="Video still of an officer inspecting a cannabis grow room">
    <div class="abs play"><svg width="24" height="24"><path d="M10 7l7 5-7 5z" fill="#333"/></svg></div>
    <div class="abs bar"><svg width="8" height="8"><path d="M1 0l7 4-7 4z" fill="#ddd"/></svg>04:59<span class="track"></span>10:35</div>
  </div>
  <h2 class="abs welcome-title">Welcome To Verdale Lodge 37</h2>
  <div class="abs rule-light"></div>
  <div class="abs welcome-copy">
    <p>Lorem ipsum dolor sit amet, consectetuer adipiscing elit, sed diam nonummy nibh euismod ut laoreet dolore magna aliquam erat volutpat. Ut wisi enim ad minim veniam, quis nostrud etation ullamcorper suscipit lobortis nisl ut aliquip ex ea commodo consequat.</p>
    <p>Duis autem vel eum iriure dor in hendrerit in vulputate velit esse molestie vel illum dolore eu feugiat nulla facilisro eros et accumsan et iusto odio dignissim qui blandit praesent luptatum zzril.</p>
    <a class="more">READ MORE »</a>
  </div>
</section>

<section>
  <div class="abs lower"></div>
  <h3 class="abs sec-title" style="left:88px;top:810px">
    <svg width="18" height="16"><rect x="0" y="0" width="12" height="9" rx="2" fill="#1a8a46"/><rect x="5" y="5" width="12" height="9" rx="2" fill="#1a8a46"/></svg>Client Testimonial</h3>
  <div class="abs rule-dark" style="left:85px;top:837px;width:282px"></div>
  <div class="abs quote"><span class="abs qmark" style="left:18px;top:12px;text-indent:0">“</span>Lorem ipsum dolor sit amet, consectetuer adipi sed diam nony nibh euismod ut laoreet dolore magna aliquam erat volut wisi enim ad minim veniam, quis nostrud etation ullamcorpecipit lobortis nisl ut aliquip ex ea commodo consequatuis autem vel eum iriure dor in hendrerit in vulputate velit esse molestie vel illum dolore <span class="qmark">”</span></div>
  <svg class="abs quote-tail" width="24" height="14"><path d="M0 0h24L20 14z" fill="#666"/></svg>
  <div class="abs author">Mr. Nisl Ut Aliquip</div>
  <div class="abs divider"></div>

  <h3 class="abs sec-title" style="left:416px;top:810px">
    <svg width="20" height="16"><path d="M2 5h5l8-4v14l-8-4H2z" fill="#1a8a46"/></svg>Latest News</h3>
  <div class="abs rule-dark" style="left:414px;top:837px;width:281px"></div>
  <div class="abs news" style="top:853px">
    <div class="date"><i></i>14-March-2014</div>
    <h4>Exerci tation ullamcorper suscipit lobortis nisl ut aliquip.</h4>
    <p>Lorem ipsum dolor sit amet, consectetuer adipiscing eli sed di nonmmy<br>nibh euismod tincidunt ut laoreet dolore ma aliquam erat volutpat.</p>
  </div>
  <div class="abs" style="left:414px;top:916px;width:281px;border-top:1px dotted #888"></div>
  <div class="abs news" style="top:929px">
    <div class="date"><i></i>14-March-2014</div>
    <h4>Mullamcorper suscipit lobortis nisl ut aliquip.</h4>
    <p>nibh euismod tincidunt ut laoreet dolore ma aliquam erat volutpat.</p>
  </div>
</section>

<footer>
  <div class="abs footer"></div>
  <form class="abs quote-panel">
    <h3><svg width="20" height="16"><path d="M1 7l9-6 9 6v8H1z" fill="none" stroke="#fff" stroke-width="1.5"/><path d="M1 7l9 5 9-5" fill="none" stroke="#fff" stroke-width="1.5"/></svg>Request a Quote</h3>
    <div class="field">Name</div>
    <div class="field">Email</div>
    <div class="field tall">Message</div>
    <div class="btn" style="width:48px;height:23px;line-height:23px;margin-top:10px">SEND</div>
  </form>

  <h3 class="abs foot-h" style="left:296px;top:1027px">News Latter Signup</h3>
  <div class="abs subscribe"><div class="input">Enter Your Email</div><div class="btn">SUBMIT</div></div>
  <div class="abs vline" style="left:563px;top:1038px;height:44px"></div>
  <h3 class="abs foot-h" style="left:590px;top:1027px">Socail Connect</h3>
  <div class="abs social" style="left:590px;top:1053px"><span></span><span></span><span></span><span></span></div>

  <div class="abs hline" style="left:296px;top:1092px;width:399px"></div>
  <div class="abs contact" style="left:297px;top:1107px;width:115px">
    <svg width="8" height="14"><path d="M4 13C1 8 0 6 0 4a4 4 0 018 0c0 2-1 4-4 9z" fill="#fff"/><circle cx="4" cy="4" r="1.5" fill="#333"/></svg>
    <span>Lorem ipsum dolor sit amet, consectetuer adipiscing eli sed di nonmmy</span>
  </div>
  <div class="abs contact" style="left:428px;top:1107px;font-size:10px">
    <svg width="8" height="12"><rect x="0" y="0" width="8" height="12" rx="1.5" fill="#fff"/><rect x="1.5" y="2" width="5" height="6" fill="#333"/></svg><span>123-555-0147</span></div>
  <div class="abs contact" style="left:428px;top:1131px">
    <svg width="10" height="9"><path d="M0 3l5-3 5 3v6H0z" fill="#fff"/><path d="M0 3l5 3 5-3" fill="none" stroke="#333"/></svg><span>info@verdalelodge37.com</span></div>
  <div class="abs vline" style="left:563px;top:1102px;height:60px"></div>
  <div class="abs foot-brand">VERDALE LODGE 37</div>

  <div class="abs hline" style="left:296px;top:1164px;width:399px"></div>
  <div class="abs copy">© 2014 Verdale Lodge 37 &nbsp;| &nbsp;All Rights Reserved</div>
</footer>

</body>
</html>
```